Tech business card design

We need an amazing business card design for our new business 'Pexla' a marketing tech startup based in Sydney, Australia. We provide an online marketplace for businesses to search and buy advertising media, connect with service providers and learn more about marketing. We wish to communicate 'cool tech', reliability and professionalism and design based around our logo.

Target Market(s)

Business Owners

Contact Information for Business Card

Name
Position
Email Address
Website
Phone Number

Font styles to use
Other font styles liked:
• Avenir & Avenir Next

Colors

Designer to choose colors to be used in the design.

```html
<!DOCTYPE html>
<html lang="en">
<head>
<meta charset="utf-8">
<title>Pexla Business Card</title>
<link rel="stylesheet" href="https://fonts.googleapis.com/css2?family=Mulish:wght@300;400;600;800&display=swap">
<style>
  :root {
    --navy: #1f1d4f;
    --ink: #2a2a3a;
    --grey: #7a7a80;
    --rule: #55555c;
    --paper: #ffffff;
    --backdrop: #e6e6e9;
  }
  * { margin: 0; padding: 0; box-sizing: border-box; }
  html, body { width: 1200px; height: 892px; overflow: hidden; }
  body {
    background: var(--backdrop);
    font-family: "Mulish", "Avenir Next", sans-serif;
    position: relative;
  }
  .card {
    position: absolute;
    width: 560px;
    height: 342px;
    background: var(--paper);
    box-shadow: 0 10px 30px rgba(0,0,0,0.18);
    overflow: hidden;
  }
  .card--front { left: 50px; top: 60px; }
  .card--back { left: 590px; top: 490px; }

  .wordmark {
    font-family: "Mulish", sans-serif;
    font-weight: 800;
    color: var(--navy);
    letter-spacing: -2px;
    line-height: 1;
  }
  .card--front .wordmark {
    position: absolute;
    left: 0; right: 0; top: 92px;
    text-align: center;
    font-size: 112px;
  }
  .front-url {
    position: absolute;
    left: 0; right: 0; top: 262px;
    text-align: center;
    font-size: 13px;
    font-weight: 300;
    letter-spacing: 9px;
    color: var(--grey);
  }

  .card--back .wordmark {
    position: absolute;
    right: 48px; top: 38px;
    font-size: 70px;
  }
  .back-rule {
    position: absolute;
    left: 40px; right: 28px; top: 206px;
    height: 1px;
    background: var(--rule);
  }
  .edge-tab {
    position: absolute;
    left: 0; top: 222px;
    width: 10px; height: 30px;
    background: var(--navy);
  }
  .holder {
    position: absolute;
    left: 44px; top: 216px;
  }
  .holder__name {
    font-size: 19px;
    font-weight: 600;
    color: var(--navy);
    letter-spacing: 0.3px;
  }
  .holder__role {
    font-size: 15px;
    font-weight: 400;
    color: var(--grey);
    letter-spacing: 0.5px;
    margin-top: 1px;
  }
  .holder__divider {
    width: 200px; height: 1px;
    background: var(--rule);
    margin: 10px 0 8px;
  }
  .contact {
    display: flex;
    align-items: center;
    gap: 10px;
    font-size: 14px;
    color: var(--ink);
    line-height: 22px;
  }
  .contact svg { width: 14px; height: 14px; flex: none; }
  .band { position: absolute; left: 0; bottom: 0; width: 560px; height: 342px; }
  .band-url {
    position: absolute;
    right: 18px; bottom: 10px;
    font-size: 12.5px;
    letter-spacing: 0.8px;
    line-height: 16px;
    color: var(--paper);
    white-space: nowrap;
  }
</style>
</head>
<body>

  <section class="card card--front" aria-label="Card front">
    <div class="wordmark">pexla</div>
    <div class="front-url">www.pexlamedia.com.au</div>
  </section>

  <section class="card card--back" aria-label="Card back">
    <div class="wordmark">pexla</div>
    <div class="back-rule"></div>
    <div class="edge-tab"></div>

    <div class="holder">
      <div class="holder__name">DANIEL MARSH</div>
      <div class="holder__role">FOUNDER, DIRECTOR</div>
      <div class="holder__divider"></div>
      <div class="contact">
        <svg viewBox="0 0 14 14" aria-hidden="true"><rect x="3" y="0.8" width="8" height="12.4" rx="1.2" fill="none" stroke="#1f1d4f" stroke-width="1.6"/><circle cx="7" cy="11" r="0.8" fill="#1f1d4f"/></svg>
        <span>+61 (0)400 555 019</span>
      </div>
      <div class="contact">
        <svg viewBox="0 0 14 14" aria-hidden="true"><path d="M1 3 H13 V11 H1 Z" fill="#1f1d4f"/><path d="M1 3 L7 8 L13 3" fill="none" stroke="#fff" stroke-width="1.2"/></svg>
        <span>daniel@pexlamedia.com.au</span>
      </div>
    </div>

    <svg class="band" viewBox="0 0 560 342" aria-hidden="true">
      <path d="M0 333 H340 C362 333 358 304 384 304 H560 V342 H0 Z" fill="#1f1d4f"/>
    </svg>
    <div class="band-url">www.pexlamedia.com.au</div>
  </section>

</body>
</html>
```